Property Finance Company - Orbin Funding Limited

Background: Orbin Funding Group Limited is a private property finance company. Orbin Funding Group has capital to directly fund first mortgage, mezzanine and preferred equity financing. We also acquire performing, sub-performing and distressed debt.

Orbin Fundings management philosophy emphasises expertise, innovation, wisdom, honesty and competitiveness. Orbin Funding are not finance brokers - we provide debt funding to the commercial property and residential development sectors. Our process is built from experience and cumutavely Orbin Fundings Directors have in excess of 60 years wisdom.

The aim of the website will be to increase brand awareness, provide clients with comfort around our level of skill and background on who we are, generate more sales, and provide examples of projects that we have funded.

The website is a new product launch, and we need to use our Orbin Funding logo that has just been designed. We like a dark background, and either black/silver/grey/ jade green, or black/gold/jade green colours.

Our unique advantages are that we have fast turnaround times, we can solve clients funding problems and we know what we are doing. Our target audience will be viewing the website on both desktop and mobile devices.

We would like to have the following pages:

Home
About
Team
Services
Project Experience
Contact

Competitors Website: http://www.tarvolo.example/

We would also like to have the option of video footage in our website, as you can see in our competitors website.

Overall we want a really slick, elegant but modern website that is better than www.tarvolo.example

Target Market(s)

Finance borrowers, property developers, accountants, lawyers, businesspeople, high net worth people

Industry/Entity Type

Finance

Requirements
Must have
• Please see project description
Nice to have
Should not have

```html
<!DOCTYPE html>
<html lang="en">
<head>
<meta charset="utf-8">
<title>Orbin Funding Group</title>
<link rel="stylesheet" href="https://fonts.googleapis.com/css2?family=Cinzel:wght@400;700&family=PT+Sans:ital,wght@0,400;0,700;1,400&display=swap">
<style>
:root{
  --green:#0ea36a;
  --green-dark:#0b8a59;
  --black:#0d0d0d;
  --ink:#1c1c1c;
  --grey-text:#6a6a6a;
  --light:#f3f3f3;
  --mid:#e5e5e5;
  --footer:#1b1e23;
  --white:#ffffff;
}
*{margin:0;padding:0;box-sizing:border-box}
html,body{width:1200px;height:4569px;overflow:hidden}
body{position:relative;background:var(--white);font-family:"PT Sans",sans-serif;color:var(--ink)}
.abs{position:absolute}
.serif{font-family:"Cinzel",serif}
.section-title{position:absolute;left:0;width:1200px;text-align:center;font-family:"Cinzel",serif;font-weight:700;font-size:42px;color:var(--ink);letter-spacing:1px}
.section-intro{position:absolute;left:150px;width:900px;text-align:center;font-size:14px;line-height:28px;color:var(--grey-text)}
.photo{position:absolute}
.btn-black{position:absolute;background:var(--black);color:var(--white);font-family:"Cinzel",serif;font-size:18px;letter-spacing:1px;display:flex;align-items:center;justify-content:center}

/* header */
.site-header{left:0;top:0;width:1200px;height:116px;background:rgba(0,0,0,.72);z-index:2}
.brand{left:75px;top:22px;width:150px;text-align:center;color:var(--white);font-family:"Cinzel",serif;font-weight:700;font-size:17px;line-height:22px}
.nav a{position:absolute;top:37px;height:43px;line-height:43px;color:var(--white);font-size:15px;text-decoration:none;text-transform:uppercase}
.nav a.active{background:var(--green);padding:0 26px}

/* hero */
.hero{left:0;top:0;width:1200px;height:676px;background:linear-gradient(100deg,#3c4550 0%,#7c8590 38%,#b9bec4 60%,#5a6068 100%)}
.hero-title{right:82px;top:290px;text-align:right;color:var(--white);font-family:"Cinzel",serif;font-weight:700;font-size:52px;line-height:64px}
.hero-sub{right:82px;top:432px;width:480px;text-align:right;color:var(--white);font-style:italic;font-size:16px;line-height:24px}
.slide-arrow{top:358px;width:52px;height:52px;border-radius:50%;background:rgba(60,60,60,.8)}

/* welcome */
.down-btn{left:576px;top:902px;width:48px;height:48px;border-radius:50%;background:var(--green)}

/* about */
.about-photo{left:0;top:1014px;width:1200px;height:539px;background:linear-gradient(110deg,#2b2f35,#6a6f77 45%,#a9aeb3 70%,#3f444b)}
.green-box{position:absolute;background:var(--green);color:var(--white)}
.green-box h2{font-family:"Cinzel",serif;font-weight:700;font-size:38px;letter-spacing:1px}
.green-box p{font-size:14px;line-height:27px}

/* services */
.service{position:absolute;top:1776px;width:300px;height:432px}
.service .img{position:absolute;left:0;top:0;width:300px;height:225px}
.service .tab{position:absolute;right:6px;top:189px;width:190px;height:36px;background:var(--green);color:var(--white);font-family:"Cinzel",serif;font-weight:700;font-size:16px;display:flex;align-items:center;justify-content:center;letter-spacing:.5px}
.service p{position:absolute;left:26px;top:252px;width:250px;font-size:13px;line-height:26px;color:var(--grey-text)}
.service .more{position:absolute;left:0;width:300px;top:2158px;text-align:center;font-family:"Cinzel",serif;font-size:15px;color:var(--ink)}
.service .more span{text-decoration:underline}

/* expertise */
.exp-icon{position:absolute;top:2356px;width:113px;height:113px;border-radius:50%;background:var(--green);box-shadow:0 12px 10px -8px rgba(0,0,0,.35)}
.exp-label{position:absolute;top:2494px;width:240px;text-align:center;font-family:"Cinzel",serif;font-size:21px;color:var(--ink);letter-spacing:1px}

/* testimonial */
.avatar{left:515px;top:3022px;width:66px;height:66px;border-radius:50%;background:#5b4637;border:3px solid var(--white)}

/* projects */
.proj-item{position:absolute;left:79px;width:500px;height:122px}
.proj-item .thumb{position:absolute;left:0;top:0;width:143px;height:122px}
.proj-item h3{position:absolute;left:161px;top:0;width:320px;font-family:"Cinzel",serif;font-weight:700;font-size:13px;line-height:22px;color:var(--white)}
.proj-item p{position:absolute;left:161px;top:48px;width:320px;font-size:13px;line-height:22px;color:var(--white)}

/* newsletter */
.email-field{left:228px;top:4097px;width:534px;height:55px;background:var(--light);font-size:13px;color:#555;padding-left:20px;line-height:55px}

/* footer */
.site-footer{left:0;top:4213px;width:1200px;height:289px;background:var(--footer)}
.foot-head{position:absolute;top:4250px;font-family:"Cinzel",serif;font-size:17px;color:var(--white);letter-spacing:1px}
.sitemap{left:344px;top:4292px;list-style:none;font-size:13px;line-height:25px;color:#d0d0d0}
.sitemap li::before{content:"› ";color:var(--white)}
.foot-thumb{position:absolute;width:73px;height:66px;border:2px solid #ddd}
.social{position:absolute;top:4405px;width:36px;height:36px;border-radius:50%;background:var(--green)}
.contact-line{position:absolute;left:910px;font-size:13px;line-height:22px;color:#d0d0d0}
.bottom-bar{left:0;top:4502px;width:1200px;height:67px;background:var(--green);color:var(--white);font-size:13px;text-align:center;line-height:67px}
</style>
</head>
<body>

<!-- hero -->
<div class="abs hero" role="img" aria-label="Photo of two business colleagues reviewing documents in a bright office"></div>
<header class="abs site-header">
  <div class="abs brand">ORBIN FUNDING<br>GROUP</div>
  <nav class="nav">
    <a class="active" style="left:472px">Home</a>
    <a style="left:600px">About</a>
    <a style="left:682px">Team</a>
    <a style="left:758px">Services</a>
    <a style="left:862px">Project Experience</a>
    <a style="left:1054px">Contact</a>
  </nav>
</header>
<div class="abs hero-title">ORBIN FUNDING<br>GROUP</div>
<p class="abs hero-sub">Orbin Funding Group has capital to directly fund first mortgage, mezzanine and preferred equity financing</p>
<div class="abs slide-arrow" style="left:14px"><svg width="52" height="52"><path d="M30 17 L21 26 L30 35" stroke="#fff" stroke-width="3" fill="none"/></svg></div>
<div class="abs slide-arrow" style="left:1134px"><svg width="52" height="52"><path d="M22 17 L31 26 L22 35" stroke="#fff" stroke-width="3" fill="none"/></svg></div>

<!-- welcome -->
<h1 class="section-title" style="top:730px">WELCOME TO ORBIN FUNDING GROUP</h1>
<p class="section-intro" style="top:800px">Lorem Ipsum is simply dummy text of the printing and typesetting industry. Lorem Ipsum has been the industry's standard dummy text ever since the 1500s, when an unknown printer took a galley of type and scrambled it to make a type specimen book. It has survived not only five centuries, but also the leap into electronic typesetting, remaining essentially unchanged.</p>
<div class="abs down-btn"><svg width="48" height="48"><path d="M18 21 L24 27 L30 21" stroke="#fff" stroke-width="3" fill="none"/></svg></div>

<!-- about -->
<div class="about-photo photo" role="img" aria-label="Photo of a business team meeting around a table with laptops"></div>
<div class="green-box" style="left:79px;top:1255px;width:676px;height:298px;padding:38px 40px">
  <h2>ABOUT US</h2>
  <p style="margin-top:14px">Lorem Ipsum is simply dummy text of the printing and typesetting industry. Lorem Ipsum has been the industry's standard dummy text ever since the 1500s, when an unknown printer took a galley of type and scrambled it to make a type specimen book. It has survived not only five centuries, but also the leap into electronic typesetting, remaining essentially unchanged.</p>
</div>
<div class="btn-black" style="left:755px;top:1499px;width:185px;height:54px">READ MORE</div>

<!-- services -->
<h2 class="section-title" style="top:1610px">SERVICES WE PROVIDE YOU</h2>
<p class="section-intro" style="top:1672px">Lorem Ipsum is simply dummy text of the printing and typesetting industry. Lorem Ipsum has been the industry's standard dummy text ever since the 1500s, when an unknown printer took a galley of type and scrambled it to make</p>

<div class="service" style="left:0;background:var(--light)">
  <div class="img" role="img" aria-label="Photo of financial charts and paperwork on a desk" style="background:linear-gradient(135deg,#8a7460,#d9d2c8)"></div>
  <div class="tab">DEBT FUNDING</div>
  <p>Lorem Ipsum is simply dummy text of the printing and typesetting industry. Lorem Ipsum has been the industry's standard dummy text</p>
</div>
<div class="service" style="left:300px;background:var(--mid)">
  <div class="img" role="img" aria-label="Photo of a warehouse interior with storage racks" style="background:linear-gradient(135deg,#5c6b78,#b5bec6)"></div>
  <div class="tab">MEZZANINE</div>
  <p>Lorem Ipsum is simply dummy text of the printing and typesetting industry. Lorem Ipsum has been the industry's standard dummy text</p>
</div>
<div class="service" style="left:600px;background:var(--light)">
  <div class="img" role="img" aria-label="Photo of a business handshake" style="background:linear-gradient(135deg,#6f7b86,#d6d9dc)"></div>
  <div class="tab">EQUITY FINANCING</div>
  <p>Lorem Ipsum is simply dummy text of the printing and typesetting industry. Lorem Ipsum has been the industry's standard dummy text</p>
</div>
<div class="service" style="left:900px;background:var(--mid)">
  <div class="img" role="img" aria-label="Photo of modern glass office towers" style="background:linear-gradient(135deg,#3d5a77,#a9bccd)"></div>
  <div class="tab">PERFORMING</div>
  <p>Lorem Ipsum is simply dummy text of the printing and typesetting industry. Lorem Ipsum has been the industry's standard dummy text</p>
</div>
<div class="abs serif" style="left:0;top:2158px;width:1200px;font-size:15px">
  <span class="abs" style="left:84px;text-decoration:underline">READ MORE...</span><span class="abs" style="left:210px">»</span>
  <span class="abs" style="left:384px;text-decoration:underline">READ MORE...</span><span class="abs" style="left:510px">»</span>
  <span class="abs" style="left:684px;text-decoration:underline">READ MORE...</span><span class="abs" style="left:810px">»</span>
  <span class="abs" style="left:984px;text-decoration:underline">READ MORE...</span><span class="abs" style="left:1110px">»</span>
</div>

<!-- expertise -->
<h2 class="section-title" style="top:2262px;font-weight:400;font-size:46px">EXPERTISE</h2>
<div class="exp-icon" style="left:233px"><svg width="113" height="113" fill="none" stroke="#fff" stroke-width="2.5"><circle cx="56" cy="50" r="16"/><path d="M49 66 h14 M50 72 h12 M56 22 v-6 M34 30 l-5 -5 M78 30 l5 -5 M28 50 h-6 M84 50 h6"/></svg></div>
<div class="exp-icon" style="left:425px"><svg width="113" height="113" fill="none" stroke="#fff" stroke-width="2.5"><path d="M56 28 v52 M36 36 h40 M36 36 l-8 20 h16 z M76 36 l-8 20 h16 z M44 82 h24"/></svg></div>
<div class="exp-icon" style="left:626px"><svg width="113" height="113" fill="none" stroke="#fff" stroke-width="2.5"><circle cx="56" cy="38" r="10"/><path d="M38 82 v-14 a18 18 0 0 1 36 0 v14 z"/></svg></div>
<div class="exp-icon" style="left:833px"><svg width="113" height="113" fill="none" stroke="#fff" stroke-width="2.5"><rect x="32" y="56" width="22" height="22"/><rect x="60" y="56" width="22" height="22"/><path d="M43 56 v-12 h28 v12 M57 44 v-12"/><circle cx="57" cy="28" r="4"/></svg></div>
<div class="exp-label" style="left:170px">INNOVATION</div>
<div class="exp-label" style="left:362px">WISDOM</div>
<div class="exp-label" style="left:563px">HONESTY</div>
<div class="exp-label" style="left:770px">COMPETITIVENESS</div>

<!-- testimonial -->
<div class="photo" style="left:0;top:2574px;width:1200px;height:539px;background:linear-gradient(100deg,#6b5a4a,#a3917c 40%,#7d7468 70%,#3f3a35)" role="img" aria-label="Photo of a smiling client holding a phone on a city street"></div>
<div class="green-box" style="left:85px;top:2818px;width:677px;height:295px;padding:34px 38px">
  <h2>WHAT OUR CLIENT SAY</h2>
  <p style="margin-top:12px">"Lorem Ipsum is simply dummy text of the printing and typesetting industry. Lorem Ipsum has been the industry's standard dummy text ever since the 1500s, when an unknown printer took a galley of type and scrambled it to make "</p>
</div>
<div class="abs avatar" role="img" aria-label="Client portrait"></div>
<div class="abs serif" style="left:598px;top:3030px;color:#fff;font-size:17px">CLIENT NAME</div>
<div class="abs" style="left:598px;top:3054px;color:#fff;font-size:12px">sample.example</div>
<div class="btn-black" style="left:762px;top:3058px;width:185px;height:55px">VIEW ALL</div>

<!-- project experience -->
<h2 class="section-title" style="top:3178px">PROJECT EXPERIENCE</h2>
<p class="section-intro" style="top:3238px">Lorem Ipsum is simply dummy text of the printing and typesetting industry. Lorem Ipsum has been the industry's standard dummy text ever since the 1500s, when an unknown printer took a galley of type and scrambled it to make</p>
<div class="abs" style="left:0;top:3351px;width:600px;height:542px;background:var(--green)"></div>
<div class="proj-item" style="top:3412px">
  <div class="thumb" role="img" aria-label="Photo of a city skyline" style="background:linear-gradient(135deg,#4a6f8e,#b7c9d6)"></div>
  <h3>LOREM IPSUM IS SIMPLY DUMMY TEXT OF THE PRINTING AND TYPESETTING</h3>
  <p>Lorem Ipsum is simply dummy text of the printing and typesetting</p>
</div>
<div class="proj-item" style="top:3552px">
  <div class="thumb" role="img" aria-label="Photo of a handshake over a desk" style="background:linear-gradient(135deg,#7f8a94,#d8dcdf)"></div>
  <h3>LOREM IPSUM IS SIMPLY DUMMY TEXT OF THE PRINTING AND TYPESETTING</h3>
  <p>Lorem Ipsum is simply dummy text of the printing and typesetting</p>
</div>
<div class="proj-item" style="top:3692px">
  <div class="thumb" role="img" aria-label="Photo of an office meeting room" style="background:linear-gradient(135deg,#8b7a64,#d6cbbd)"></div>
  <h3>LOREM IPSUM IS SIMPLY DUMMY TEXT OF THE PRINTING AND TYPESETTING</h3>
  <p>Lorem Ipsum is simply dummy text of the printing and typesetting</p>
</div>
<div class="btn-black" style="left:350px;top:3838px;width:250px;height:55px">VIEW ALL PROJECTS</div>
<div class="photo" style="left:600px;top:3351px;width:600px;height:542px;background:linear-gradient(120deg,#3a3f46,#8d949b 50%,#c9cdd1)" role="img" aria-label="Video still of a conference room meeting"></div>
<svg class="abs" style="left:880px;top:3608px" width="70" height="70"><circle cx="35" cy="35" r="33" fill="rgba(0,0,0,.55)" stroke="#fff" stroke-width="2"/><path d="M27 22 L50 35 L27 48 Z" fill="#fff"/></svg>

<!-- newsletter -->
<h2 class="section-title" style="top:3952px">SIGN UP FOR NEWSLETTER</h2>
<p class="section-intro" style="top:4010px;left:300px;width:600px">Lorem Ipsum is simply dummy text of the printing and typesetting industry. Lorem Ipsum has been the industry's standard dummy text ever since the printer took a galley of type and scrambled it to make</p>
<div class="abs email-field">Enter Your Email *</div>
<svg class="abs" style="left:735px;top:4118px" width="16" height="12"><rect x="0" y="0" width="16" height="12" fill="var(--green)"/><path d="M0 0 L8 7 L16 0" stroke="#fff" stroke-width="1.5" fill="none"/></svg>
<div class="btn-black" style="left:786px;top:4097px;width:271px;height:55px;font-weight:700">SUBSCRIBE</div>

<!-- footer -->
<footer class="abs site-footer" role="img" aria-label="Dark city skyline backdrop"></footer>
<div class="abs serif" style="left:80px;top:4300px;width:170px;text-align:center;color:#fff;font-weight:700;font-size:22px;line-height:28px">ORBIN FUNDING<br>GROUP</div>
<div class="social" style="left:142px"></div>
<div class="social" style="left:186px"></div>
<div class="social" style="left:230px"></div>

<div class="foot-head" style="left:344px">SITEMAP</div>
<ul class="abs sitemap">
  <li>Home</li><li>About</li><li>Team</li><li>Services</li><li>Project Experience</li><li>Contact</li>
</ul>

<div class="foot-head" style="left:600px">PROJECTS</div>
<div class="foot-thumb" style="left:600px;top:4297px;background:linear-gradient(135deg,#4a6f8e,#b7c9d6)" role="img" aria-label="Project photo"></div>
<div class="foot-thumb" style="left:686px;top:4297px;background:linear-gradient(135deg,#8b7a64,#d6cbbd)" role="img" aria-label="Project photo"></div>
<div class="foot-thumb" style="left:772px;top:4297px;background:linear-gradient(135deg,#5c6b78,#b5bec6)" role="img" aria-label="Project photo"></div>
<div class="foot-thumb" style="left:600px;top:4383px;background:linear-gradient(135deg,#7f8a94,#d8dcdf)" role="img" aria-label="Project photo"></div>
<div class="foot-thumb" style="left:686px;top:4383px;background:linear-gradient(135deg,#a08866,#e0d4c0)" role="img" aria-label="Project photo"></div>
<div class="foot-thumb" style="left:772px;top:4383px;background:linear-gradient(135deg,#3d5a77,#a9bccd)" role="img" aria-label="Project photo"></div>

<div class="foot-head" style="left:874px">CONTACT US</div>
<svg class="abs" style="left:874px;top:4296px" width="20" height="26"><path d="M10 25 C4 16 2 12 2 9 a8 8 0 0 1 16 0 c0 3 -2 7 -8 16z" fill="var(--green)"/><circle cx="10" cy="9" r="3" fill="var(--footer)"/></svg>
<div class="contact-line" style="top:4294px;color:var(--green);font-size:12px">ORBIN FUNDING GROUP</div>
<div class="contact-line" style="top:4316px;width:230px">101 - Lorem Ipsum is simple dummy text of print text</div>
<svg class="abs" style="left:874px;top:4393px" width="20" height="20"><path d="M4 2 l4 0 l2 5 l-3 2 a11 11 0 0 0 5 5 l2 -3 l5 2 l0 4 a2 2 0 0 1 -2 2 A16 16 0 0 1 2 4 a2 2 0 0 1 2 -2z" fill="var(--green)"/></svg>
<div class="contact-line" style="top:4392px">123 456 7890</div>
<svg class="abs" style="left:874px;top:4440px" width="20" height="14"><rect width="20" height="14" fill="var(--green)"/><path d="M0 0 L10 8 L20 0" stroke="var(--footer)" stroke-width="1.5" fill="none"/></svg>
<div class="contact-line" style="top:4436px">info@orbinfundinggroup.example</div>

<div class="abs bottom-bar">©ORBIN FUNDING GROUP - 2017 All Right Reserved.</div>

</body>
</html>
```